A clean crisp business card for a Landscape Construction company. Designed to be easy to read contact/ info and also be appealing/interesting, unlike a traditional business card.

Industry/Entity Type

Landscape Construction

Contact Information for Business Card

Company name : Brambleford Landscape Construction, phone number: (877) 62Vista, website:Bramblefordyards.example, Email, sales@bramblefordyards.example

Requirements
Nice to have
• Luxurious finishes/ details…. Icons or emblems next to contact info
Should not have
• Clipart or general pictures

```html
<!DOCTYPE html>
<html lang="en">
<head>
<meta charset="utf-8">
<title>Brambleford Landscape Construction – Business Card</title>
<link rel="stylesheet" href="https://fonts.googleapis.com/css2?family=Cinzel:wght@600;700&family=Arimo:wght@400&display=swap">
<style>
  :root {
    --brand-blue: #2a6fc2;
    --brand-blue-deep: #1f5eae;
    --leaf-green: #8dc63f;
    --paper: #ffffff;
    --ink: #1a1a1a;
    --stage: #2b2b2b;
  }
  * { box-sizing: border-box; margin: 0; padding: 0; }
  html, body { width: 1200px; height: 900px; overflow: hidden; }
  body {
    background: var(--stage);
    display: flex;
    align-items: center;
    justify-content: center;
    gap: 90px;
    font-family: "Arimo", Arial, sans-serif;
  }
  .card {
    width: 380px;
    height: 665px;
    border-radius: 22px;
    overflow: hidden;
    position: relative;
  }
  /* Back */
  .card--back {
    background: linear-gradient(160deg, var(--brand-blue) 0%, var(--brand-blue-deep) 100%);
    display: flex;
    align-items: center;
    justify-content: center;
  }
  .card--back .brand-mark { color: var(--paper); }
  .brand-mark {
    font-family: "Cinzel", Georgia, serif;
    font-weight: 700;
    text-align: center;
    line-height: 1.25;
    display: flex;
    flex-direction: column;
    align-items: center;
    gap: 14px;
  }
  .brand-mark__dot {
    width: 46px; height: 46px; border-radius: 50%;
    background: currentColor;
  }
  .brand-mark__name { font-size: 34px; letter-spacing: 1px; }
  .brand-mark__sub { font-size: 15px; letter-spacing: 3px; }
  /* Front */
  .card--front {
    background: var(--paper);
    display: flex;
    flex-direction: column;
  }
  .card--front .brand-mark {
    color: var(--brand-blue);
    height: 300px;
    justify-content: center;
  }
  .name-band {
    background: var(--brand-blue);
    color: var(--paper);
    height: 120px;
    display: flex;
    flex-direction: column;
    justify-content: center;
    align-items: center;
  }
  .name-band__name {
    font-family: "Cinzel", Georgia, serif;
    font-weight: 700;
    font-size: 30px;
    letter-spacing: 1px;
  }
  .name-band__role { font-size: 17px; margin-top: 4px; }
  .contact {
    flex: 1;
    padding: 30px 44px 0;
    display: flex;
    flex-direction: column;
    align-items: center;
    color: var(--ink);
  }
  .contact__rule {
    width: 100%;
    height: 1.5px;
    background: var(--leaf-green);
  }
  .contact__icons {
    display: flex; gap: 8px; margin: 18px 0 12px;
  }
  .contact__icon {
    width: 20px; height: 20px; border-radius: 4px;
    background: var(--brand-blue);
  }
  .contact__line { font-size: 18px; line-height: 1.45; text-align: center; }
  .contact__list { margin-bottom: 20px; }
</style>
</head>
<body>
  <section class="card card--back" role="img" aria-label="Blue card back with a faint repeating pattern of the company emblem">
    <div class="brand-mark">
      <span class="brand-mark__dot"></span>
      <span class="brand-mark__name">BRAMBLEFORD</span>
      <span class="brand-mark__sub">LANDSCAPE CONSTRUCTION</span>
    </div>
  </section>

  <section class="card card--front">
    <div class="brand-mark">
      <span class="brand-mark__dot"></span>
      <span class="brand-mark__name">BRAMBLEFORD</span>
      <span class="brand-mark__sub">LANDSCAPE CONSTRUCTION</span>
    </div>
    <div class="name-band">
      <span class="name-band__name">OWEN HARTLEY</span>
      <span class="name-band__role">Founder</span>
    </div>
    <div class="contact">
      <div class="contact__rule"></div>
      <div class="contact__icons">
        <span class="contact__icon"></span>
        <span class="contact__icon"></span>
        <span class="contact__icon"></span>
      </div>
      <div class="contact__list">
        <p class="contact__line">(877) 62Vista</p>
        <p class="contact__line">sales@bramblefordyards.example</p>
        <p class="contact__line">bramblefordyards.example</p>
      </div>
      <div class="contact__rule"></div>
    </div>
  </section>
</body>
</html>
```